KBT Business Cards

We require business cards for our business. We would like a matte black back to the card, with our logo centred in the middle. The front side of the card is open to design.

Target Market(s)

Clients looking for legal services (professional)

Industry/Entity Type

Legal

Contact Information for Business Card

Doran Kelbrath
Partner
Mobile: 0461 738 524
Email: doran@kbtlaw.co
Website: www.kbtlaw.co
Level 3, 118 Wendmore Street
Sydney NSW 2000

Font styles to use
Other font styles liked:
• Avenir

Colors
f04a50
ffffff
1b1b1b

Requirements
Must have
• Black back with logo included in the centre of the card.
• Our font is Avenir.

```html
<!DOCTYPE html>
<html lang="en">
<head>
<meta charset="UTF-8">
<title>KBT Legal Business Cards</title>
<link href="https://fonts.googleapis.com/css2?family=Nunito+Sans:wght@300;400;600;800&display=swap" rel="stylesheet">
<style>
  :root {
    --brand-red: #f04a50;
    --brand-red-deep: #c8143f;
    --brand-red-shade: #8f0f2e;
    --ink: #1b1b1b;
    --paper: #ffffff;
    --backdrop: #2b2b2b;
  }
  * { margin: 0; padding: 0; box-sizing: border-box; }
  html, body {
    width: 1200px;
    height: 960px;
    overflow: hidden;
    background: var(--backdrop);
    font-family: "Nunito Sans", "Avenir", Arial, sans-serif;
  }
  .canvas { position: relative; width: 1200px; height: 960px; }

  .card {
    position: absolute;
    width: 620px;
    height: 378px;
    overflow: hidden;
    box-shadow: 0 18px 40px rgba(0,0,0,0.45);
  }

  /* Back of card */
  .card-back { left: 500px; top: 80px; background: var(--ink); }
  .back-brand {
    position: absolute;
    inset: 0;
    display: flex;
    align-items: center;
    justify-content: center;
    gap: 22px;
  }
  .brand-square {
    width: 54px; height: 54px;
    background: var(--brand-red-deep);
  }
  .back-brand .brand-name {
    color: var(--paper);
    font-weight: 800;
    font-size: 52px;
    letter-spacing: 1px;
    line-height: 1;
  }

  /* Front of card */
  .card-front { left: 80px; top: 500px; background: var(--paper); }
  .front-shapes { position: absolute; inset: 0; }
  .front-brand {
    position: absolute;
    left: 44px; top: 96px;
    display: flex;
    align-items: center;
    gap: 14px;
  }
  .front-brand .brand-square { width: 36px; height: 36px; }
  .front-brand .brand-name {
    color: var(--ink);
    font-weight: 800;
    font-size: 32px;
    letter-spacing: 0.5px;
    line-height: 1;
  }

  .holder {
    position: absolute;
    right: 22px; top: 74px;
    text-align: right;
    color: var(--paper);
  }
  .holder-name { font-weight: 800; font-size: 20px; letter-spacing: 0.6px; line-height: 1.1; }
  .holder-role { font-weight: 400; font-size: 14px; letter-spacing: 1px; margin-top: 2px; }

  .contact {
    position: absolute;
    right: 22px; top: 168px;
    color: var(--paper);
    font-weight: 400;
    font-size: 15px;
    text-align: right;
    line-height: 24px;
  }
  .contact-line { display: flex; justify-content: flex-end; align-items: center; gap: 8px; }
  .contact-line svg { width: 14px; height: 14px; flex: none; }
  .address { margin-top: 8px; padding-right: 22px; }
</style>
</head>
<body>
<main class="canvas">

  <section class="card card-back" aria-label="Card back">
    <div class="back-brand">
      <span class="brand-square"></span>
      <span class="brand-name">KBT LEGAL</span>
    </div>
  </section>

  <section class="card card-front" aria-label="Card front">
    <svg class="front-shapes" viewBox="0 0 620 378" width="620" height="378" aria-hidden="true">
      <defs>
        <linearGradient id="bandGradient" x1="0" y1="0" x2="1" y2="0">
          <stop offset="0" stop-color="#e8234f"/>
          <stop offset="1" stop-color="#b8123d"/>
        </linearGradient>
      </defs>
      <polygon points="330,0 620,0 620,378 196,378" fill="var(--ink)"/>
      <polygon points="332,64 346,74 346,128 332,118" fill="var(--brand-red-shade)"/>
      <rect x="346" y="74" width="274" height="54" fill="url(#bandGradient)"/>
      <polygon points="332,64 606,64 620,74 346,74" fill="#f0335c"/>
    </svg>

    <div class="front-brand">
      <span class="brand-square"></span>
      <span class="brand-name">KBT LEGAL</span>
    </div>

    <div class="holder">
      <p class="holder-name">DORAN KELBRATH</p>
      <p class="holder-role">PARTNER</p>
    </div>

    <div class="contact">
      <p class="contact-line">0461 738 524
        <svg viewBox="0 0 14 14"><circle cx="7" cy="7" r="6.3" fill="none" stroke="#fff" stroke-width="1.2"/><rect x="5" y="3.5" width="4" height="7" rx="0.8" fill="none" stroke="#fff" stroke-width="1"/></svg>
      </p>
      <p class="contact-line">doran@kbtlaw.co
        <svg viewBox="0 0 14 14"><rect x="1" y="3" width="12" height="8" fill="#fff"/><polyline points="1,3 7,8 13,3" fill="none" stroke="#1b1b1b" stroke-width="1"/></svg>
      </p>
      <p class="contact-line">www.kbtlaw.co
        <svg viewBox="0 0 14 14"><circle cx="7" cy="7" r="6" fill="none" stroke="#fff" stroke-width="1.2"/><ellipse cx="7" cy="7" rx="2.6" ry="6" fill="none" stroke="#fff" stroke-width="1"/><line x1="1" y1="7" x2="13" y2="7" stroke="#fff" stroke-width="1"/></svg>
      </p>
      <p class="address">Level 3, 118 Wendmore Street<br>Sydney NSW 2000</p>
    </div>
  </section>

</main>
</body>
</html>
```